Card design for orthopaedic surgeons working as The Brightwater Joint Centre

Business cards, letterhead

Colors

Designer to choose colors to be used in the design.

Requirements
Must have
• Late addition.
• Cards letterhead must have logos of
• Crestmoor Lindell College of Surgeons
• Varenwood Bone Health Association
Nice to have
• Back of card to have space for appointment time to be added by hand and some blank space for writing incidental other notes.

```html
<!DOCTYPE html>
<html lang="en">
<head>
<meta charset="utf-8">
<title>The Brightwater Joint Centre – Stationery</title>
<link href="https://fonts.googleapis.com/css2?family=Roboto:wght@300;400;500&display=swap" rel="stylesheet">
<style>
  :root {
    --backdrop: #c8c8c8;
    --paper: #ffffff;
    --navy: #0a2d47;
    --sky: #4aa3df;
    --ink: #1d2a36;
    --badge-warm: #c98a4a;
    --badge-cool: #8aa0b8;
  }
  * { box-sizing: border-box; margin: 0; padding: 0; }
  html, body { width: 1200px; height: 763px; overflow: hidden; }
  body {
    background: var(--backdrop);
    font-family: "Roboto", Arial, sans-serif;
    color: var(--ink);
    position: relative;
  }
  .sheet, .card {
    position: absolute;
    background: var(--paper);
    overflow: hidden;
    box-shadow: 0 1px 3px rgba(0,0,0,0.25);
  }
  .letterhead { left: 47px; top: 12px; width: 579px; height: 735px; }
  .card { border-radius: 12px; width: 441px; height: 254px; left: 659px; }
  .card-front { top: 114px; }
  .card-back { top: 401px; }

  .brand {
    position: absolute;
    font-weight: 400;
    color: var(--sky);
    white-space: nowrap;
    letter-spacing: -0.2px;
    line-height: 1;
  }
  .badge { position: absolute; border-radius: 6px; }
  .badge-college { background: linear-gradient(180deg, var(--badge-warm), #b8473c); }
  .badge-association { background: linear-gradient(180deg, var(--badge-cool), #5a6f88); }

  .contact-list { position: absolute; list-style: none; font-weight: 300; color: var(--ink); }
  .contact-list li { display: flex; align-items: center; gap: 3px; white-space: nowrap; }
  .contact-list svg { flex: none; }
  .address { position: absolute; text-align: right; font-weight: 300; white-space: nowrap; }

  .wave { position: absolute; left: 0; bottom: 0; display: block; }

  .person-name { position: absolute; left: 20px; top: 125px; font-size: 14.5px; font-weight: 500; color: var(--navy); }
  .person-role { position: absolute; left: 20px; top: 142px; font-size: 11px; color: var(--sky); }

  .appt-title { position: absolute; left: 21px; top: 88px; font-size: 14px; font-weight: 500; color: var(--navy); }
  .appt-title span { color: var(--sky); }
  .appt-field { position: absolute; left: 21px; font-size: 12px; font-weight: 300; white-space: nowrap; display: flex; align-items: center; }
  .dots { display: inline-block; border-bottom: 1px dotted var(--ink); height: 1px; margin: 6px 6px 0 3px; }
  .box { display: inline-block; width: 8px; height: 8px; border: 1.4px solid var(--ink); margin: 0 2px 0 0; }
  .choice { margin-right: 9px; display: inline-flex; align-items: center; }
  .appt-note { position: absolute; left: 20px; top: 225px; font-size: 11px; color: var(--sky); white-space: nowrap; }
</style>
</head>
<body>

<!-- Letterhead -->
<section class="sheet letterhead">
  <div class="brand" style="left:37px; top:62px; font-size:18px;">The Brightwater Joint Centre</div>
  <div class="badge badge-college" style="left:384px; top:15px; width:64px; height:71px;" role="img" aria-label="Crestmoor Lindell College of Surgeons crest"></div>
  <div class="badge badge-association" style="left:468px; top:15px; width:72px; height:71px;" role="img" aria-label="Varenwood Bone Health Association fellowship badge"></div>

  <ul class="contact-list" style="left:37px; top:658px; font-size:10.5px; line-height:14px;">
    <li><svg width="7" height="7" viewBox="0 0 10 10"><path d="M2 0l2 2-1 2c1 1 2 2 3 3l2-1 2 2-2 2C4 10 0 6 0 2z" fill="var(--sky)"/></svg>555 014 2280</li>
    <li><svg width="8" height="6" viewBox="0 0 10 7"><rect width="10" height="7" fill="var(--sky)"/><path d="M0 0l5 4 5-4" stroke="#fff" fill="none"/></svg>hello@brightwaterjoint.com</li>
    <li><svg width="7" height="7" viewBox="0 0 10 10"><circle cx="5" cy="5" r="4.3" fill="none" stroke="var(--sky)" stroke-width="1.2"/><path d="M1 5h8M5 1v8" stroke="var(--sky)" stroke-width="1"/></svg>www.brightwaterjoint.com</li>
  </ul>
  <div class="address" style="right:37px; top:658px; font-size:10.5px; line-height:15px;">48 Harlow Ridge Drive<br>Suite 310, Ashford, MI 48211</div>

  <svg class="wave" width="579" height="48" viewBox="0 0 579 48" preserveAspectRatio="none">
    <path d="M0 4 C110 44 250 38 370 18 C460 4 530 8 579 28 L579 48 L0 48Z" fill="var(--navy)"/>
    <path d="M0 4 C110 44 250 38 370 18 C460 4 530 8 579 28 L579 32 C530 14 460 10 370 24 C250 44 110 48 0 6Z" fill="var(--sky)"/>
  </svg>
</section>

<!-- Business card front -->
<section class="card card-front">
  <div class="brand" style="left:20px; top:51px; font-size:15px;">The Brightwater Joint Centre</div>
  <div class="badge badge-college" style="left:265px; top:17px; width:62px; height:68px;" role="img" aria-label="Crestmoor Lindell College of Surgeons crest"></div>
  <div class="badge badge-association" style="left:351px; top:17px; width:70px; height:68px;" role="img" aria-label="Varenwood Bone Health Association fellowship badge"></div>

  <div class="person-name">Adrian Callow</div>
  <div class="person-role">President</div>

  <ul class="contact-list" style="left:20px; top:180px; font-size:11.5px; line-height:16px;">
    <li><svg width="7" height="7" viewBox="0 0 10 10"><path d="M2 0l2 2-1 2c1 1 2 2 3 3l2-1 2 2-2 2C4 10 0 6 0 2z" fill="var(--sky)"/></svg>555 014 2280</li>
    <li><svg width="8" height="6" viewBox="0 0 10 7"><rect width="10" height="7" fill="var(--sky)"/><path d="M0 0l5 4 5-4" stroke="#fff" fill="none"/></svg>hello@brightwaterjoint.com</li>
    <li><svg width="7" height="7" viewBox="0 0 10 10"><circle cx="5" cy="5" r="4.3" fill="none" stroke="var(--sky)" stroke-width="1.2"/><path d="M1 5h8M5 1v8" stroke="var(--sky)" stroke-width="1"/></svg>www.brightwaterjoint.com</li>
  </ul>
  <div class="address" style="right:20px; top:180px; font-size:10.5px; line-height:14px;">48 Harlow Ridge Drive<br>Suite 310, Ashford, MI 48211</div>

  <svg class="wave" width="441" height="36" viewBox="0 0 441 36" preserveAspectRatio="none">
    <path d="M0 2 C80 34 190 30 290 14 C360 3 410 6 441 22 L441 36 L0 36Z" fill="var(--navy)"/>
    <path d="M0 2 C80 34 190 30 290 14 C360 3 410 6 441 22 L441 26 C410 10 360 7 290 19 C190 34 80 38 0 4Z" fill="var(--sky)"/>
  </svg>
</section>

<!-- Business card back -->
<section class="card card-back">
  <div class="brand" style="left:21px; top:33px; font-size:15.5px;">The Brightwater Joint Centre</div>

  <div class="appt-title"><span>Next</span> Appointment</div>

  <div class="appt-field" style="top:127px;">Name:<span class="dots" style="width:190px;"></span></div>
  <div class="appt-field" style="top:151px;">Time:<span class="dots" style="width:124px;"></span>
    <span class="choice"><span class="box"></span>AM</span><span class="choice"><span class="box"></span>PM</span></div>
  <div class="appt-field" style="top:175px;">Date:<span class="dots" style="width:200px;"></span></div>
  <div class="appt-field" style="top:199px;">
    <span class="choice"><span class="box"></span>MON</span>
    <span class="choice"><span class="box"></span>TUE</span>
    <span class="choice"><span class="box"></span>WED</span>
    <span class="choice"><span class="box"></span>THU</span>
    <span class="choice"><span class="box"></span>FRI</span>
    <span class="choice"><span class="box"></span>SAT</span>
  </div>
  <div class="appt-note">If you are unable to keep your appointment, please call us as soon as possible</div>
</section>

</body>
</html>
```